Website Development for vaultmerrow.com.au

Build a new Wordpress/Responsive website for vaultmerrow.com.au

Target Market(s)

Compliance Managers, Risk Managers, Information Security and Cyber Security Professionals, Chief Data/Digital Officers, Chief Operating/Financial Officers, Business Continuity Professionals, Disaster Recovery Planners, Small Business Owners, Local/Federal Government entities

Industry/Entity Type

Data Service

Coding

Coded - Design and coding required

Number of Pages Required

5+ page

Font styles to use
Sans Serif

Colors

Designer to choose colors to be used in the design.

Requirements
Must have
• 1. Site Structure: Home Page plus the following chapter-pages for a) Services b) About c) Resources d) Blog e) Contact Us
• 2. Prefer site to built on wordpress and we can purchase a theme if needed (we currently use Kelp9 for other sites)
• 3. Blog needs to be wordpress based
• 4. We will host the site ourselves on our own servers
• 5. Responsive Design
Nice to have
• 1. Livechat capability/interface
• 2. Capability for marketing automation integration (such as hubspot, marketo, infusionsoft etc)
• 3. Capability for CRM integration (Salesforce)

```html
<!DOCTYPE html>
<html lang="en">
<head>
<meta charset="utf-8">
<title>Vault Merrow — Security Aware</title>
<link rel="stylesheet" href="https://fonts.googleapis.com/css2?family=Montserrat:wght@400;500;600;700&family=Open+Sans:wght@400;600&display=swap">
<style>
:root{
  --red:#e01b22;
  --red-dark:#b80f15;
  --ink:#2b2b2b;
  --text:#555;
  --muted:#8a8a8a;
  --line:#dcdcdc;
  --grey-bg:#efefef;
  --white:#fff;
  --bar:#5a5a5a;
}
*{box-sizing:border-box;margin:0;padding:0}
html,body{width:1200px;height:3509px;overflow:hidden}
body{position:relative;background:var(--white);font-family:"Open Sans",Arial,sans-serif;color:var(--text)}
.section{position:absolute;left:0;width:1200px}
.heading{position:absolute;left:0;width:1200px;text-align:center;font-family:"Montserrat",Arial,sans-serif;font-size:30px;font-weight:400;letter-spacing:1px;color:var(--ink)}
.heading b{color:var(--red);font-weight:700}
.heading::after{content:"";display:block;width:90px;height:2px;background:var(--line);margin:14px auto 0}

/* header */
.site-header{top:0;height:105px;background:var(--white)}
.brand{position:absolute;left:140px;top:22px;display:flex;align-items:center;gap:10px}
.brand-mark{width:34px;height:34px;background:var(--red);border-radius:4px}
.brand-name{font-family:"Montserrat",Arial,sans-serif;font-weight:700;font-size:30px;color:var(--red)}
.topbar{position:absolute;left:720px;top:0;width:363px;height:33px;background:var(--bar);clip-path:polygon(0 0,100% 0,97% 100%,4% 100%);display:flex;align-items:center;gap:28px;padding-left:24px;color:var(--white);font-size:13px}
.topbar span{display:flex;align-items:center;gap:7px}
.nav{position:absolute;top:72px;left:531px;display:flex;font-family:"Montserrat",Arial,sans-serif;font-size:13px;color:var(--ink);letter-spacing:.5px}
.nav a{position:absolute;white-space:nowrap;text-decoration:none;color:inherit}
.nav a.active{color:var(--red);font-weight:600;border-bottom:2px solid var(--red);padding-bottom:4px}

/* hero */
.hero{top:105px;height:494px;background:linear-gradient(100deg,#c40f16 0%,#e8262d 45%,#d91820 75%,#b50d13 100%)}
.hero-art{position:absolute;left:630px;top:25px;width:495px;height:460px;border-radius:40% 40% 30% 30%;background:radial-gradient(circle at 45% 40%,rgba(255,255,255,.55) 0%,rgba(255,210,210,.35) 35%,rgba(200,20,30,0) 70%)}
.hero-title{position:absolute;left:140px;top:152px;color:var(--white);font-family:"Montserrat",Arial,sans-serif}
.hero-title .l1{font-size:33px;font-weight:700}
.hero-title .l2{font-size:34px;font-weight:400;letter-spacing:2px;margin-top:8px}
.btn-ghost{position:absolute;left:140px;top:283px;width:199px;height:40px;border-radius:20px;background:rgba(255,255,255,.25);color:var(--white);font-family:"Montserrat",Arial,sans-serif;font-weight:700;font-size:13px;letter-spacing:1px;display:flex;align-items:center;justify-content:center}

/* about */
.about{top:599px;height:458px}
.about .heading{top:72px}
.about .heading span{font-size:20px;color:var(--muted);font-weight:400;letter-spacing:2px}
.lead{position:absolute;left:140px;top:132px;width:920px;text-align:center;font-size:12px;line-height:20px}
.goal{position:absolute;top:240px;width:380px;display:flex;gap:14px}
.goal svg{flex:none}
.goal h3{font-family:"Montserrat",Arial,sans-serif;font-weight:500;font-size:18px;color:var(--ink);margin-bottom:6px}
.goal p{font-size:12px;line-height:18px}
.btn-red{position:absolute;left:537px;top:348px;width:126px;height:36px;border-radius:18px;background:var(--red);color:var(--white);font-family:"Montserrat",Arial,sans-serif;font-size:13px;font-weight:700;display:flex;align-items:center;gap:10px;padding-left:8px}
.btn-red i{width:22px;height:22px;background:var(--white);border-radius:50%}

/* services */
.services{top:1057px;height:517px;background:var(--grey-bg)}
.services .heading{top:62px}
.card{position:absolute;top:138px;width:206px;height:293px;background:var(--white);border-radius:6px;box-shadow:0 2px 8px rgba(0,0,0,.12);text-align:center}
.card .photo{height:143px;border-radius:6px 6px 0 0}
.card .badge{position:absolute;left:84px;top:118px;width:38px;height:38px;border-radius:50%;background:var(--white);border:1px solid var(--line)}
.card h4{margin-top:24px;font-family:"Montserrat",Arial,sans-serif;font-weight:700;font-size:14px;line-height:20px;color:var(--ink)}
.card p{margin:8px 14px 0;font-size:12px;line-height:17px}
.card .plus{position:absolute;left:92px;bottom:-11px;width:22px;height:22px;border-radius:50%;background:#555;color:var(--white);font-weight:700;font-size:18px;line-height:22px}
.card .plus.red{background:var(--red)}

/* serve */
.serve{top:1574px;height:484px}
.serve .heading{top:68px}
.serve .sub{position:absolute;top:128px;width:1200px;text-align:center;font-size:12px}
.aud{position:absolute;top:192px;width:200px;text-align:center}
.aud .ring{width:140px;height:140px;margin:0 auto;border-radius:50%;background:var(--white);box-shadow:0 3px 12px rgba(0,0,0,.12);display:flex;align-items:center;justify-content:center}
.aud.active .ring{border:3px solid var(--red);width:146px;height:146px}
.aud span{display:block;margin-top:40px;font-family:"Montserrat",Arial,sans-serif;font-size:16px;line-height:22px;color:var(--ink)}
.aud.active span{color:var(--red);font-weight:600;margin-top:34px}
.arrow-btn{position:absolute;top:246px;width:34px;height:34px;border-radius:50%;background:var(--white);box-shadow:0 1px 6px rgba(0,0,0,.2);display:flex;align-items:center;justify-content:center}

/* team */
.team{top:2058px;height:487px;background:var(--grey-bg)}
.team .heading{top:64px}
.member{position:absolute;top:136px;width:175px;text-align:center}
.member .photo{height:178px;border:2px solid #d6d6d6;background:linear-gradient(180deg,#f5f5f5 0%,#cfcfcf 100%)}
.member.active .photo{border:3px solid var(--red)}
.member h5{margin-top:14px;font-family:"Montserrat",Arial,sans-serif;font-size:15px;font-weight:600;letter-spacing:1px;color:#555}
.member small{display:block;margin-top:4px;font-size:12px;color:var(--muted)}
.socials{display:flex;gap:8px;justify-content:center;margin-top:14px}
.socials i{width:26px;height:26px;border-radius:50%;background:#c4c4c4}
.member.active .socials i{background:var(--red)}

/* blog */
.blog{top:2545px;height:601px}
.blog .heading{top:68px}
.post{position:absolute;top:145px;width:290px}
.post .photo{height:210px}
.post .date{position:absolute;left:6px;top:0;width:40px;height:46px;background:var(--red);color:var(--white);font-family:"Montserrat",Arial,sans-serif;font-size:12px;line-height:16px;padding:6px 0 0 6px}
.post .date b{display:block;font-size:15px}
.post h4{margin-top:20px;font-family:"Montserrat",Arial,sans-serif;font-size:13px;line-height:19px;font-weight:700;color:var(--red)}
.post p{margin-top:10px;font-size:12px;line-height:18px}
.post .more{display:flex;align-items:center;gap:8px;margin-top:16px;font-size:13px;color:var(--red);font-weight:600}

/* footer */
.site-footer{top:3146px;height:327px;background:linear-gradient(90deg,#d6141b 0%,#e52229 60%,#cc121a 100%);color:var(--white)}
.col-title{position:absolute;top:60px;font-family:"Montserrat",Arial,sans-serif;font-size:14px;font-weight:700;letter-spacing:1px}
.links{position:absolute;left:143px;top:96px;list-style:none;font-size:12px;line-height:29px}
.links li::before{content:"›";margin-right:12px}
.field{position:absolute;height:28px;background:var(--white);color:#888;font-size:11px;padding:6px 6px;border-radius:2px}
.submit{position:absolute;left:339px;top:232px;width:120px;height:28px;background:#8b8b8b;border:1px solid #ddd;text-align:center;font-family:"Montserrat",Arial,sans-serif;font-weight:700;font-size:12px;line-height:26px;letter-spacing:1px}
.contact{position:absolute;left:821px;top:94px;font-size:12px;line-height:17px}
.contact div{display:flex;gap:12px;margin-bottom:16px}
.contact .socials i{background:transparent;border:2px solid var(--white);width:28px;height:28px}
.bottom-bar{top:3473px;height:36px;background:#5c5c5c;color:#ddd;font-size:11px;line-height:36px;padding-left:143px}
.chat{position:absolute;left:1020px;top:3460px;width:42px;height:42px;border-radius:50%;background:var(--red);display:flex;align-items:center;justify-content:center}
</style>
</head>
<body>

<header class="section site-header">
  <div class="brand"><span class="brand-mark"></span><span class="brand-name">Vault Merrow</span></div>
  <div class="topbar">
    <span><svg width="13" height="13" viewBox="0 0 24 24"><path fill="#fff" d="M6.6 10.8a15 15 0 006.6 6.6l2.2-2.2c.3-.3.7-.4 1-.2 1.1.4 2.3.6 3.6.6.6 0 1 .4 1 1V20c0 .6-.4 1-1 1A17 17 0 013 4c0-.6.4-1 1-1h3.5c.6 0 1 .4 1 1 0 1.3.2 2.5.6 3.6.1.3 0 .7-.2 1z"/></svg>123-456-7890</span>
    <span><svg width="13" height="11" viewBox="0 0 24 18"><rect x="1" y="1" width="22" height="16" rx="2" fill="none" stroke="#fff" stroke-width="2"/><path d="M1 2l11 8 11-8" fill="none" stroke="#fff" stroke-width="2"/></svg>info@vaultmerrow.com.au</span>
  </div>
  <nav class="nav">
    <a class="active" style="left:0">HOME</a>
    <a style="left:94px">ABOUT</a>
    <a style="left:187px">SERVICES</a>
    <a style="left:292px">RESOURCES</a>
    <a style="left:386px">BLOG</a>
    <a style="left:484px">CONTACT US</a>
  </nav>
</header>

<section class="section hero">
  <div class="hero-art" role="img" aria-label="Hand holding a glowing globe of digital security icons"></div>
  <h1 class="hero-title"><div class="l1">Because We Care, We're</div><div class="l2">SECURITY AWARE</div></h1>
  <div class="btn-ghost">CONTACT US TODAY</div>
</section>

<section class="section about">
  <h2 class="heading"><b>About Vault</b> <span>MERROW</span></h2>
  <p class="lead">Lorem ipsum dolor sit amet, consectetuer adipiscing elit, sed diam nonummy nibh euismod tincidunt ut laoreet dolore magna aliquam erat volutpat. Ut wisi enim ad minim veniam, quis nostrud exerci tation ullamcorper suscipit lobortis nisl ut aliquip ex ea commodo consequat. Duis autem vel eum iriure dolor in hendrerit in vulputate velit esse molestie consequat, vel illum dolore eu feugiat nulla facilisis at vero eros et accumsan et iusto odio dignissim qui blandit praesent luptatum zzril delenit augue duis dolore te feugait nulla facilisi nonummy nibh euismod tincidunt ut laoreet dolore magna aliquam.</p>
  <div class="goal" style="left:156px">
    <svg width="50" height="50" viewBox="0 0 50 50"><circle cx="24" cy="26" r="20" fill="none" stroke="#e01b22" stroke-width="3"/><circle cx="24" cy="26" r="12" fill="none" stroke="#e01b22" stroke-width="3"/><circle cx="24" cy="26" r="4" fill="#e01b22"/><path d="M24 26L44 6M38 6h6v6" stroke="#e01b22" stroke-width="3" fill="none"/></svg>
    <div><h3>Our Mission</h3><p>Lamcorper suscipit lobortis nisl ut aliquip ex ea commodo consequat. Duis autem vel eum iriure dolor in hendrerit in vulputate velit esse molestie consequat, vel</p></div>
  </div>
  <div class="goal" style="left:632px">
    <svg width="50" height="50" viewBox="0 0 50 50"><path d="M3 25C10 13 18 9 25 9s15 4 22 16c-7 12-15 16-22 16S10 37 3 25z" fill="none" stroke="#e01b22" stroke-width="3"/><circle cx="25" cy="25" r="8" fill="none" stroke="#e01b22" stroke-width="3"/><circle cx="25" cy="25" r="3" fill="#e01b22"/></svg>
    <div><h3>Our Vision</h3><p>Lamcorper suscipit lobortis nisl ut aliquip ex ea commodo consequat. Duis autem vel eum iriure dolor in hendrerit in vulputate velit esse molestie consequat, vel</p></div>
  </div>
  <div class="btn-red"><i></i>Read More</div>
</section>

<section class="section services">
  <h2 class="heading"><b>OUR</b> SERVICES</h2>
  <div class="card" style="left:143px"><div class="photo" role="img" aria-label="Blue data centre server illustration" style="background:linear-gradient(160deg,#1a6fb5,#0b2d5a)"></div><i class="badge"></i><h4>Data Management<br>Services</h4><p>Lorem ipsum dolor sit amet consectetuer adipiscing elit, sed diam nonummy nibh eui.</p><div class="plus red">+</div></div>
  <div class="card" style="left:377px"><div class="photo" role="img" aria-label="Hand touching a digital analytics screen" style="background:linear-gradient(160deg,#2a5f95,#8fb3d6)"></div><i class="badge"></i><h4>Data Management<br>Platforms</h4><p>Lorem ipsum dolor sit amet consectetuer adipiscing elit, sed diam nonummy nibh eui.</p><div class="plus">+</div></div>
  <div class="card" style="left:612px"><div class="photo" role="img" aria-label="Engineer inspecting an industrial site" style="background:linear-gradient(160deg,#5b6e55,#2f3a36)"></div><i class="badge"></i><h4>Industry<br>Solutions</h4><p>Lorem ipsum dolor sit amet consectetuer adipiscing elit, sed diam nonummy nibh eui.</p><div class="plus">+</div></div>
  <div class="card" style="left:847px"><div class="photo" role="img" aria-label="Digital padlock on a circuit background" style="background:linear-gradient(160deg,#1d4b6e,#5fa6c9)"></div><i class="badge"></i><h4>Ransomware<br>Protection</h4><p>Lorem ipsum dolor sit amet consectetuer adipiscing elit, sed diam nonummy nibh eui.</p><div class="plus">+</div></div>
</section>

<section class="section serve">
  <h2 class="heading"><b>TO WHOM</b> WE SERVE</h2>
  <p class="sub">Lorem ipsum dolor sit amet, consectetuer adipiscing elit, sed diam nonummy nibh euismod tincidunt ut laoreet dolore magna aliquam erat</p>
  <div class="arrow-btn" style="left:77px"><svg width="10" height="12" viewBox="0 0 10 12"><path d="M8 1L2 6l6 5" stroke="#888" stroke-width="2" fill="none"/></svg></div>
  <div class="arrow-btn" style="left:1089px"><svg width="10" height="12" viewBox="0 0 10 12"><path d="M2 1l6 5-6 5" stroke="#888" stroke-width="2" fill="none"/></svg></div>
  <div class="aud" style="left:113px"><div class="ring"><svg width="54" height="54" viewBox="0 0 54 54" fill="none" stroke="#888" stroke-width="2"><path d="M22 6L3 42h38z"/><path d="M22 18v12M22 35v2"/><circle cx="40" cy="40" r="9" fill="#fff"/><circle cx="40" cy="37" r="3"/><path d="M34 46c2-4 10-4 12 0"/></svg></div><span>Risk Managers</span></div>
  <div class="aud" style="left:305px"><div class="ring"><svg width="50" height="54" viewBox="0 0 50 54" fill="none" stroke="#888" stroke-width="2"><path d="M25 3L5 11v16c0 12 9 21 20 24 11-3 20-12 20-24V11z"/><path d="M15 27l7 7 13-14"/></svg></div><span>Information<br>Security</span></div>
  <div class="aud active" style="left:496px"><div class="ring"><svg width="56" height="56" viewBox="0 0 56 56" fill="none" stroke="#e01b22" stroke-width="2"><rect x="12" y="12" width="32" height="32" rx="3"/><path d="M20 12V5M28 12V5M36 12V5M20 51v-7M28 51v-7M36 51v-7M12 20H5M12 28H5M12 36H5M51 20h-7M51 28h-7M51 36h-7"/><rect x="21" y="27" width="14" height="10"/><path d="M24 27v-4a4 4 0 018 0v4"/></svg></div><span>Cyber Security<br>Professionals</span></div>
  <div class="aud" style="left:693px"><div class="ring"><svg width="54" height="54" viewBox="0 0 54 54" fill="none" stroke="#888" stroke-width="2"><circle cx="27" cy="14" r="7"/><path d="M15 34c2-8 22-8 24 0"/><rect x="10" y="34" width="34" height="16"/><path d="M40 8l6-4M42 14h7"/></svg></div><span>Chief Data<br>Technicians</span></div>
  <div class="aud" style="left:885px"><div class="ring"><svg width="50" height="54" viewBox="0 0 50 54" fill="none" stroke="#888" stroke-width="2"><path d="M14 14h22M16 14c0-6 4-10 9-10s9 4 9 10"/><path d="M16 16c0 7 4 12 9 12s9-5 9-12"/><path d="M8 50c0-12 8-18 17-18s17 6 17 18z"/><path d="M20 38h10v6H20z"/></svg></div><span>Digital<br>Officers</span></div>
</section>

<section class="section team">
  <h2 class="heading"><b>OUR</b> TEAM</h2>
  <svg style="position:absolute;left:70px;top:220px" width="24" height="60" viewBox="0 0 24 60"><path d="M22 2L3 30l19 28" stroke="#bbb" stroke-width="2" fill="none"/></svg>
  <svg style="position:absolute;left:1106px;top:220px" width="24" height="60" viewBox="0 0 24 60"><path d="M2 2l19 28L2 58" stroke="#bbb" stroke-width="2" fill="none"/></svg>
  <div class="member active" style="left:157px"><div class="photo" role="img" aria-label="Portrait of team member in a suit and red tie"></div><h5>CORIN ALDANE</h5><small>Designation</small><div class="socials"><i></i><i></i><i></i><i></i></div></div>
  <div class="member" style="left:393px"><div class="photo" role="img" aria-label="Portrait of team member in a dark blazer"></div><h5>MIRA TOLENO</h5><small>Designation</small><div class="socials"><i></i><i></i><i></i><i></i></div></div>
  <div class="member" style="left:632px"><div class="photo" role="img" aria-label="Portrait of team member in a dark suit"></div><h5>CORIN ALDANE</h5><small>Designation</small><div class="socials"><i></i><i></i><i></i><i></i></div></div>
  <div class="member" style="left:868px"><div class="photo" role="img" aria-label="Portrait of senior team member with glasses"></div><h5>EDMUND VARLEY</h5><small>Designation</small><div class="socials"><i></i><i></i><i></i><i></i></div></div>
</section>

<section class="section blog">
  <h2 class="heading"><b>LATEST BLOG</b> POSTS</h2>
  <article class="post" style="left:143px"><div class="photo" role="img" aria-label="Business team gathered around a table" style="background:linear-gradient(180deg,#e9e9e9,#7d838c)"></div><div class="date">FEB<b>07</b></div><h4>Lorem ipsum dolor sit amet, consectetuer adipiscing elit, sed diam nonummy</h4><p>olore magna aliquam erat volutpat. Ut wisi enim minim veniam, quis nostrud exerci tationcorper suscipit lobortis nisl ut aliquip ex ea</p><div class="more">Read More <svg width="20" height="10" viewBox="0 0 20 10"><path d="M0 5h18M14 1l4 4-4 4" stroke="#555" stroke-width="1.5" fill="none"/></svg></div></article>
  <article class="post" style="left:454px"><div class="photo" role="img" aria-label="Overhead view of a team planning at a desk" style="background:linear-gradient(180deg,#c9d4de,#8d9aa6)"></div><div class="date">FEB<b>07</b></div><h4>Lorem ipsum dolor sit amet, consectetuer adipiscing elit, sed diam nonummy</h4><p>olore magna aliquam erat volutpat. Ut wisi enim minim veniam, quis nostrud exerci tationcorper suscipit lobortis nisl ut aliquip ex ea</p><div class="more">Read More <svg width="20" height="10" viewBox="0 0 20 10"><path d="M0 5h18M14 1l4 4-4 4" stroke="#555" stroke-width="1.5" fill="none"/></svg></div></article>
  <article class="post" style="left:765px"><div class="photo" role="img" aria-label="Open plan office with people at computers" style="background:linear-gradient(180deg,#dcd6cc,#9b9288)"></div><div class="date">FEB<b>07</b></div><h4>Lorem ipsum dolor sit amet, consectetuer adipiscing elit, sed diam nonummy</h4><p>olore magna aliquam erat volutpat. Ut wisi enim minim veniam, quis nostrud exerci tationcorper suscipit lobortis nisl ut aliquip ex ea</p><div class="more">Read More <svg width="20" height="10" viewBox="0 0 20 10"><path d="M0 5h18M14 1l4 4-4 4" stroke="#555" stroke-width="1.5" fill="none"/></svg></div></article>
</section>

<footer class="section site-footer">
  <div class="col-title" style="left:143px">QUICK LINKS</div>
  <ul class="links"><li>Home</li><li>About</li><li>Services</li><li>Resources</li><li>Blog</li><li>Contact Us</li></ul>
  <div class="col-title" style="left:339px">QUICK INQUIRY</div>
  <div class="field" style="left:339px;top:96px;width:194px">First Name</div>
  <div class="field" style="left:543px;top:96px;width:194px">Last Name</div>
  <div class="field" style="left:339px;top:132px;width:194px">Phone</div>
  <div class="field" style="left:543px;top:132px;width:194px">Email</div>
  <div class="field" style="left:339px;top:170px;width:398px;height:52px">Message</div>
  <div class="submit">SUBMIT</div>
  <div class="col-title" style="left:821px">CONTACT DETAILS</div>
  <div class="contact">
    <div><svg width="12" height="16" viewBox="0 0 12 16"><path d="M6 0a6 6 0 00-6 6c0 4.5 6 10 6 10s6-5.5 6-10a6 6 0 00-6-6zm0 8.5A2.5 2.5 0 116 3.5a2.5 2.5 0 010 5z" fill="#fff"/></svg><span><b>VAULT MERROW</b><br>1234 Loren Ipsum Dolor sit amet mopwe<br>ocmety Somet CA 123</span></div>
    <div><svg width="13" height="13" viewBox="0 0 24 24"><path fill="#fff" d="M6.6 10.8a15 15 0 006.6 6.6l2.2-2.2c.3-.3.7-.4 1-.2 1.1.4 2.3.6 3.6.6.6 0 1 .4 1 1V20c0 .6-.4 1-1 1A17 17 0 013 4c0-.6.4-1 1-1h3.5c.6 0 1 .4 1 1 0 1.3.2 2.5.6 3.6.1.3 0 .7-.2 1z"/></svg>123-456-7890</div>
    <div><svg width="13" height="11" viewBox="0 0 24 18"><rect x="1" y="1" width="22" height="16" rx="2" fill="none" stroke="#fff" stroke-width="2"/><path d="M1 2l11 8 11-8" fill="none" stroke="#fff" stroke-width="2"/></svg>info@vaultmerrow.com.au</div>
    <div class="socials" style="justify-content:flex-start"><i></i><i></i><i></i><i></i></div>
  </div>
</footer>
<div class="section bottom-bar">Copyright 2019 © Vault Merrow. All Rights Reserved. &nbsp;|&nbsp; Terms of services / Privacy Policy</div>
<div class="chat"><svg width="20" height="18" viewBox="0 0 20 18"><path d="M2 1h16a1 1 0 011 1v10a1 1 0 01-1 1H8l-4 4v-4H2a1 1 0 01-1-1V2a1 1 0 011-1z" fill="#fff"/><circle cx="6" cy="7" r="1.3" fill="#e01b22"/><circle cx="10" cy="7" r="1.3" fill="#e01b22"/><circle cx="14" cy="7" r="1.3" fill="#e01b22"/></svg></div>

</body>
</html>
```